Meadowlark Hollow Candle Company needs a Label design

We need a label design for a new candle company based in Charleston South Carolina. Our mission is to provide people with candles that will fill any space with fragrances that are uplifting, comforting, fresh and will make any space feel like home. Our candles are aromatherapy, 100% soy wax, and hand poured (we would love for this to be indicated somewhere on the label). We would like to see a label that is modern, very clean and uses pastel colors like green, blush pink, mauve and blush blue. The final design should communicate peace, gratitude, hope, and happiness.

```html
<!DOCTYPE html>
<html lang="en">
<head>
<meta charset="utf-8">
<title>Meadowlark Hollow Candle Company – Lavender Vanilla Label</title>
<link rel="stylesheet" href="https://fonts.googleapis.com/css2?family=Jost:wght@400;500&family=Great+Vibes&display=swap">
<style>
  :root {
    --page-bg: #f9f8f3;
    --label-bg: #fdfdfc;
    --label-edge: #ecece8;
    --brand-dot: #a9c3c1;
    --ink: #575757;
  }
  * { box-sizing: border-box; margin: 0; padding: 0; }
  html, body {
    width: 1200px;
    height: 900px;
    overflow: hidden;
    background: var(--page-bg);
  }
  .canvas {
    width: 1200px;
    height: 900px;
    display: flex;
    align-items: center;
    justify-content: center;
  }
  .label {
    width: 860px;
    height: 660px;
    background: var(--label-bg);
    border: 1px solid var(--label-edge);
    border-radius: 90px;
    display: flex;
    flex-direction: column;
    align-items: center;
    padding-top: 56px;
  }
  .brand {
    display: flex;
    flex-direction: column;
    align-items: center;
    gap: 22px;
  }
  .brand-dot {
    width: 220px;
    height: 220px;
    border-radius: 50%;
    background: var(--brand-dot);
  }
  .brand-name {
    font-family: "Jost", sans-serif;
    font-weight: 400;
    font-size: 22px;
    letter-spacing: 0.22em;
    text-transform: uppercase;
    color: var(--ink);
  }
  .scent-name {
    font-family: "Great Vibes", cursive;
    font-size: 118px;
    line-height: 1;
    color: var(--ink);
    margin-top: 28px;
  }
  .claims {
    display: flex;
    align-items: stretch;
    margin-top: 36px;
    font-family: "Jost", sans-serif;
    font-weight: 500;
    font-size: 30px;
    line-height: 1.1;
    letter-spacing: 0.04em;
    text-transform: uppercase;
    color: var(--ink);
    text-align: center;
  }
  .claim { padding: 0 44px; }
  .claim-divider {
    width: 2px;
    background: var(--ink);
  }
</style>
</head>
<body>
  <main class="canvas">
    <section class="label">
      <header class="brand">
        <div class="brand-dot" aria-hidden="true"></div>
        <p class="brand-name">Meadowlark Hollow Candle Co.</p>
      </header>
      <h1 class="scent-name">Lavender Vanilla</h1>
      <div class="claims">
        <p class="claim">Hand Poured<br>100% Soy Wax</p>
        <span class="claim-divider" aria-hidden="true"></span>
        <p class="claim">All Natural<br>Aromatherapy</p>
      </div>
    </section>
  </main>
</body>
</html>
```